Marlith Construction Core Values Wall Design

Core Values Wall Design for our Wall, I’m not exactly sure visually what we would want it to look like. Maybe some acrylic stand offs that could go on brick? If that’s a possibility. That’s where we have the most space in the office. But we could do other locations too.

These are our core values
• Safety
• Integrity
• Quality
• Client-Focused Solutions
• Continuous Improvement
• Positive Culture and Stewardship

Our vision/mission statement is Craft Assured.

```html
<!DOCTYPE html>
<html lang="en">
<head>
<meta charset="utf-8">
<title>Marlith Construction – Core Values</title>
<link href="https://fonts.googleapis.com/css2?family=Montserrat:wght@500;600;800&display=swap" rel="stylesheet">
<style>
  :root {
    --red: #e3262f;
    --blue: #1d5fa8;
    --ink: #1b1b1f;
    --sky: #a9c3e6;
    --mist: #eef0f4;
    --blush: #dcbcc3;
    --rule: rgba(255,255,255,0.75);
  }
  * { box-sizing: border-box; margin: 0; padding: 0; }
  html, body { width: 1121px; height: 1200px; overflow: hidden; }
  body { font-family: "Montserrat", sans-serif; color: var(--ink); }
  .poster {
    position: relative;
    width: 1121px; height: 1200px;
    background: linear-gradient(150deg, var(--sky) 0%, #c9d7ec 28%, var(--mist) 55%, #e8dadd 78%, var(--blush) 100%);
  }
  .title {
    position: absolute; left: 72px; top: 62px;
    font-weight: 800; font-size: 128px; line-height: 0.82; letter-spacing: -5px;
  }
  .title .line-red { color: var(--red); display: block; }
  .title .line-blue { color: var(--blue); display: block; }
  .brand-name {
    position: absolute; right: 100px; top: 104px;
    font-weight: 800; font-size: 48px; letter-spacing: 3px; text-transform: uppercase;
    color: var(--blue);
  }
  .values {
    position: absolute; left: 62px; top: 392px; width: 950px;
    display: grid; grid-template-columns: repeat(3, 1fr); grid-template-rows: 262px 285px;
  }
  .value {
    display: flex; flex-direction: column; align-items: center;
    padding-top: 30px; text-align: center;
    font-weight: 500; font-size: 27px; line-height: 1.3;
  }
  .value:nth-child(-n+3) { border-bottom: 1px solid var(--rule); }
  .value:not(:nth-child(3n)) { border-right: 1px solid var(--rule); }
  .value:nth-child(n+4) { padding-top: 46px; }
  .value-icon { width: 104px; height: 104px; margin-bottom: 30px; }
  .value-name { max-width: 260px; }
  .company-name {
    position: absolute; left: 42px; top: 1040px;
    font-weight: 800; font-size: 22px; color: var(--blue);
  }
  .mission {
    position: absolute; right: 330px; top: 1030px; text-align: right;
  }
  .mission-label { font-weight: 500; font-size: 20px; letter-spacing: 0.5px; }
  .mission-text { font-weight: 500; font-size: 30px; margin-top: 2px; }
  .mission-icon { position: absolute; left: 810px; top: 990px; width: 175px; height: 150px; }
</style>
</head>
<body>
<main class="poster">
  <h1 class="title"><span class="line-red">Core</span><span class="line-blue">Values</span></h1>
  <div class="brand-name">Craft Assured</div>

  <section class="values">
    <div class="value">
      <svg class="value-icon" viewBox="0 0 100 100" aria-hidden="true">
        <circle cx="50" cy="50" r="50" fill="var(--blue)"/>
        <circle cx="50" cy="42" r="20" fill="none" stroke="#fff" stroke-width="4"/>
        <circle cx="50" cy="42" r="12" fill="#fff"/>
        <path d="M50 35l2.5 5 5.5.8-4 3.9.9 5.5L50 47.6 45.1 50.2l.9-5.5-4-3.9 5.5-.8z" fill="var(--blue)"/>
        <path d="M40 60l-4 16 7-3 4 6 3-14M60 60l4 16-7-3-4 6-3-14" fill="#fff"/>
      </svg>
      <span class="value-name">Quality</span>
    </div>
    <div class="value">
      <svg class="value-icon" viewBox="0 0 100 100" aria-hidden="true">
        <circle cx="50" cy="50" r="50" fill="var(--red)"/>
        <path d="M14 44l12-10 10 4 10-4 10 0 8-2 14 10-6 8-20 14c-3 2-6 1-8-1l-10-8-14-4z" fill="#fff"/>
        <path d="M46 38l-8 8c-2 2 1 5 4 3l8-6" fill="none" stroke="var(--red)" stroke-width="3" stroke-linecap="round"/>
        <path d="M48 56l6 6M54 52l6 6M60 48l5 5" stroke="var(--red)" stroke-width="3" stroke-linecap="round"/>
      </svg>
      <span class="value-name">Client Focused Solutions</span>
    </div>
    <div class="value">
      <svg class="value-icon" viewBox="0 0 100 100" aria-hidden="true">
        <circle cx="50" cy="50" r="50" fill="var(--blue)"/>
        <path d="M50 74L28 52c-8-8-6-22 6-24 7-1 12 3 16 8 4-5 9-9 16-8 12 2 14 16 6 24z" fill="#fff"/>
      </svg>
      <span class="value-name">Integrity</span>
    </div>
    <div class="value">
      <svg class="value-icon" viewBox="0 0 100 100" aria-hidden="true">
        <circle cx="50" cy="50" r="50" fill="var(--red)"/>
        <rect x="24" y="46" width="12" height="24" rx="2" fill="#fff"/>
        <path d="M40 46l10-20c2-4 8-3 8 2l-2 12h14c4 0 6 3 5 6l-4 20c-1 3-3 4-6 4H40z" fill="#fff"/>
      </svg>
      <span class="value-name">Positive Culture and Stewardship</span>
    </div>
    <div class="value">
      <svg class="value-icon" viewBox="0 0 100 100" aria-hidden="true">
        <circle cx="50" cy="50" r="50" fill="var(--blue)"/>
        <path d="M50 20l24 8v18c0 16-10 26-24 32-14-6-24-16-24-32V28z" fill="#fff"/>
        <path d="M39 48l8 8 15-15" fill="none" stroke="var(--blue)" stroke-width="6" stroke-linecap="round" stroke-linejoin="round"/>
      </svg>
      <span class="value-name">Safety</span>
    </div>
    <div class="value">
      <svg class="value-icon" viewBox="0 0 100 100" aria-hidden="true">
        <circle cx="50" cy="50" r="50" fill="var(--red)"/>
        <rect x="26" y="54" width="9" height="16" fill="#fff"/>
        <rect x="40" y="46" width="9" height="24" fill="#fff"/>
        <rect x="54" y="50" width="9" height="20" fill="#fff"/>
        <rect x="68" y="40" width="9" height="30" fill="#fff"/>
        <path d="M24 46l16-10 12 6 20-14" fill="none" stroke="#fff" stroke-width="3.5"/>
        <path d="M66 24l10 2-4 9z" fill="#fff"/>
        <rect x="22" y="72" width="58" height="3" fill="#fff"/>
      </svg>
      <span class="value-name">Continuous Improvement</span>
    </div>
  </section>

  <div class="company-name">Marlith Construction</div>

  <div class="mission">
    <p class="mission-label">Our Mission</p>
    <p class="mission-text">Craft Assured</p>
  </div>
  <svg class="mission-icon" viewBox="0 0 175 150" aria-hidden="true">
    <circle cx="65" cy="85" r="56" fill="none" stroke="var(--ink)" stroke-width="13"/>
    <circle cx="65" cy="85" r="32" fill="none" stroke="var(--ink)" stroke-width="11"/>
    <circle cx="65" cy="85" r="10" fill="var(--ink)"/>
    <path d="M65 85L135 22" stroke="var(--ink)" stroke-width="9" stroke-linecap="round"/>
    <path d="M118 30l18-26 4 20 26 4-22 20z" fill="var(--ink)"/>
  </svg>
</main>
</body>
</html>
```